Nutritional Company Label and Box

Design for bottle label and box for nutritional supplement products. This will be a boilerplate for use on different vitamin product types. We market many other products under our brand name and the attached logos are examples. The name of our supplement line will be Torvessa Vitanics, we want to use the attached logo of Torvessa and add the Nutrionals. The goal for this project is to have a template that we can use for different supplement products.

Target Market(s)

Health Products

Industry/Entity Type

Vitamin

Logo Text

Torvessa Vitanicals

Font styles to use
Sans Serif

Colors

Designer to choose colors to be used in the design.

Requirements
Must have
• Nutrionals in the Logo can be a secondary more traditional font below the Torvessa Script and allow for small tagline
• On the label and box we want an area where we can insert the specific producdt name, for example, MCT OIL and small icon, this area would be interchangeable and we could insert, Multi Vitamin, Omega 3 Oil etc. within this main design. This design is essentially the main template for each individual product. Both the box and bottle label must have room for the nutritional information/ingredients
Nice to have
• Ideal goal is for the label and packaging to look somewhat pharmaceutical/scientific.
• We like the packaging for Brelo Naturals supplements seen on Quendrix. https://www.quendrixmart.example/s?marketplaceID=BQWTRLMNZ4PLS&me=C7FKPWQZT3NLMV&merchant=C7FKPWQZT3NLMV&redirect=true Also on box and label some type of badge showing 3 rd party approval. We like the color palettes used in the Brelo Naturals packaging.

```html
<!DOCTYPE html>
<html lang="en">
<head>
<meta charset="utf-8">
<title>Torvessa Vitanics – Supplement Label Template</title>
<link href="https://fonts.googleapis.com/css2?family=PT+Serif:wght@400;700&display=swap" rel="stylesheet">
<style>
  :root {
    --page: #ffffff;
    --paper: #ffffff;
    --ink-brand: #6b4a2e;
    --accent-green: #8cc63f;
    --icon-ring: #e9f3dc;
    --text-light: #ffffff;
    --bullet-text: #f3f0f7;
    --shield-gold: #d9b54a;
    --shield-edge: #b58f2a;

    --mct-band: #1f7fc6;
    --mct-lower: #2aa9e0;
    --omega-band: #5b3a8e;
    --omega-lower: #8f64ad;
    --multi-band: #3f6e57;
    --multi-lower: #f29a2c;
  }

  html, body {
    margin: 0;
    padding: 0;
    width: 1200px;
    height: 1199px;
    overflow: hidden;
    background: var(--page);
  }

  .canvas {
    position: relative;
    width: 1200px;
    height: 1199px;
  }

  .label {
    position: absolute;
    width: 17.5em;
    height: 21.4em;
    font-family: "PT Serif", Georgia, serif;
    font-size: 16px;
    background: var(--paper);
    box-shadow: 0 10px 30px rgba(0, 0, 0, 0.12);
    display: flex;
    flex-direction: column;
    overflow: hidden;
  }

  .label--mct   { left: 120px; top: 440px; --band: var(--mct-band);   --lower: var(--mct-lower); }
  .label--omega { left: 410px; top: 375px; font-size: 21.7px; --band: var(--omega-band); --lower: var(--omega-lower); z-index: 2; }
  .label--multi { left: 800px; top: 440px; --band: var(--multi-band); --lower: var(--multi-lower); }

  .label__brand {
    height: 9.6em;
    display: flex;
    align-items: flex-start;
    justify-content: center;
    padding-top: 2.2em;
    box-sizing: border-box;
    flex-shrink: 0;
  }

  .brand-name {
    margin: 0;
    color: var(--ink-brand);
    font-weight: 400;
    text-align: center;
    line-height: 1.1;
  }

  .brand-name__main {
    display: block;
    font-size: 1.7em;
    letter-spacing: 0.02em;
  }

  .brand-name__line {
    display: block;
    font-size: 1.05em;
    letter-spacing: 0.08em;
    margin-top: 0.2em;
    padding-left: 2.4em;
  }

  .label__band {
    position: relative;
    height: 6.4em;
    flex-shrink: 0;
    background: var(--band);
    display: flex;
    align-items: flex-end;
    justify-content: center;
    padding: 0 0.4em 0.9em 2.6em;
    box-sizing: border-box;
  }

  .label__band::before {
    content: "";
    position: absolute;
    left: 1.8em;
    top: 0;
    bottom: 0;
    width: 0.35em;
    background: var(--accent-green);
  }

  .product-icon {
    position: absolute;
    left: 50%;
    top: -2.4em;
    width: 4.6em;
    height: 4.6em;
    transform: translateX(-50%);
    border-radius: 50%;
    background: var(--accent-green);
    border: 0.22em solid var(--icon-ring);
    box-sizing: border-box;
    display: flex;
    align-items: center;
    justify-content: center;
  }

  .product-icon svg { width: 2.3em; height: 2.3em; }

  .product-icon__placeholder {
    width: 2.4em;
    height: 1.4em;
    border-radius: 50%;
    background: #8c5ab0;
  }

  .product-name {
    margin: 0;
    color: var(--text-light);
    font-weight: 700;
    font-size: 1.4em;
    letter-spacing: 0.02em;
    white-space: nowrap;
  }

  .label--omega .product-name { font-size: 1.38em; letter-spacing: 0.01em; }

  .label__details {
    position: relative;
    flex: 1;
    background: var(--lower);
    padding: 0.7em 0 0 3.4em;
    box-sizing: border-box;
  }

  .benefits {
    list-style: none;
    margin: 0;
    padding: 0;
  }

  .benefits li {
    position: relative;
    color: var(--bullet-text);
    font-size: 0.72em;
    line-height: 1.8;
    white-space: nowrap;
  }

  .benefits li::before {
    content: "";
    position: absolute;
    left: -1.5em;
    top: 0.7em;
    width: 0.5em;
    height: 0.5em;
    background: var(--accent-green);
  }

  .quality-seal {
    position: absolute;
    right: 1.2em;
    top: 0.55em;
    width: 3em;
    height: 3.3em;
  }
</style>
</head>
<body>
<main class="canvas">

  <article class="label label--mct">
    <header class="label__brand">
      <p class="brand-name"><span class="brand-name__main">Torvessa</span><span class="brand-name__line">VITANICS</span></p>
    </header>
    <section class="label__band">
      <div class="product-icon">
        <svg viewBox="0 0 40 40" aria-hidden="true">
          <path d="M16 8 C10 18 7 22 7 27 a9 9 0 0 0 18 0 C25 22 22 18 16 8Z" fill="#27a2e0" stroke="#fff" stroke-width="1.5"/>
          <path d="M29 10 C26 15 25 17 25 19 a4 4 0 0 0 8 0 C33 17 32 15 29 10Z" fill="#27a2e0" stroke="#fff" stroke-width="1.2"/>
        </svg>
      </div>
      <h2 class="product-name">MCT OIL</h2>
    </section>
    <section class="label__details">
      <ul class="benefits">
        <li>Weight management</li>
        <li>Healthy fats</li>
        <li>Natural Energy</li>
      </ul>
      <svg class="quality-seal" viewBox="0 0 40 44" role="img" aria-label="Third-party quality seal">
        <path d="M20 2 L37 7 V22 C37 32 29 39 20 42 C11 39 3 32 3 22 V7Z" fill="var(--shield-gold)" stroke="var(--shield-edge)" stroke-width="1.5"/>
      </svg>
    </section>
  </article>

  <article class="label label--omega">
    <header class="label__brand">
      <p class="brand-name"><span class="brand-name__main">Torvessa</span><span class="brand-name__line">VITANICS</span></p>
    </header>
    <section class="label__band">
      <div class="product-icon" role="img" aria-label="Fish icon">
        <span class="product-icon__placeholder"></span>
      </div>
      <h2 class="product-name">OMEGA 3 FISH OIL</h2>
    </section>
    <section class="label__details">
      <ul class="benefits">
        <li>Suppports heart health</li>
        <li>Purified to remove mercury</li>
        <li>High in EPA and DHA</li>
      </ul>
      <svg class="quality-seal" viewBox="0 0 40 44" role="img" aria-label="Third-party quality seal">
        <path d="M20 2 L37 7 V22 C37 32 29 39 20 42 C11 39 3 32 3 22 V7Z" fill="var(--shield-gold)" stroke="var(--shield-edge)" stroke-width="1.5"/>
      </svg>
    </section>
  </article>

  <article class="label label--multi">
    <header class="label__brand">
      <p class="brand-name"><span class="brand-name__main">Torvessa</span><span class="brand-name__line">VITANICS</span></p>
    </header>
    <section class="label__band">
      <div class="product-icon">
        <svg viewBox="0 0 40 40" aria-hidden="true">
          <path d="M14 14 h6 v7 h7 v6 h-7 v7 h-6 v-7 h-7 v-6 h7Z" fill="#f29a2c" stroke="#fff" stroke-width="1.2"/>
          <path d="M27 6 h3 v4 h4 v3 h-4 v4 h-3 v-4 h-4 v-3 h4Z" fill="#f29a2c" stroke="#fff" stroke-width="0.8"/>
          <path d="M19 5 h2 v2.5 h2.5 v2 h-2.5 v2.5 h-2 v-2.5 h-2.5 v-2 h2.5Z" fill="#f29a2c" stroke="#fff" stroke-width="0.6"/>
        </svg>
      </div>
      <h2 class="product-name">MULTI VITAMIN</h2>
    </section>
    <section class="label__details">
      <ul class="benefits">
        <li>Supports Muscle Function</li>
        <li>29 Nutrients</li>
        <li>Body ready active forms</li>
      </ul>
      <svg class="quality-seal" viewBox="0 0 40 44" role="img" aria-label="Third-party quality seal">
        <path d="M20 2 L37 7 V22 C37 32 29 39 20 42 C11 39 3 32 3 22 V7Z" fill="var(--shield-gold)" stroke="var(--shield-edge)" stroke-width="1.5"/>
      </svg>
    </section>
  </article>

</main>
</body>
</html>
```